BRISKEL Need a luxury modern business card designed.

Need a luxury modern business card designed. refer to the uploaded files for the company name and logo in the zip file under source files. i will making my descion on monday. so please send in before then so if we need to edit we will have the time. we have a trade show coming up and im on a deadline for printer.

Target Market(s)

high end clients

Contact Information for Business Card

Company nAme and logo. Tobias Fennick Co-Founder / Project Manager Office # 555-318-7094 Cell # 555-642-1586 BRISKEL.CA Tobias@briskel-example.ca

Font styles to use
Other font styles liked:
• Modern

Requirements
Must have
• Company name and logo, contact info, using the black, gold and white color scheme.

```html
<!DOCTYPE html>
<html lang="en">
<head>
<meta charset="utf-8">
<title>BRISKEL Business Card</title>
<link href="https://fonts.googleapis.com/css2?family=Montserrat:wght@300;400;500;600&display=swap" rel="stylesheet">
<style>
  :root {
    --bg: #1b1b1b;
    --charcoal: #303030;
    --ink: #2a2a2a;
    --gold: #a8986a;
    --white: #ffffff;
    --grey: #8a8a8a;
  }
  * { box-sizing: border-box; margin: 0; padding: 0; }
  html, body { width: 1200px; height: 900px; overflow: hidden; background: var(--bg); }
  body { font-family: "Montserrat", sans-serif; position: relative; }

  .card {
    position: absolute; left: 290px; width: 620px; height: 354px;
    overflow: hidden; box-shadow: 0 12px 30px rgba(0,0,0,.5);
  }
  .card--back { top: 66px; background: var(--charcoal); }
  .card--front { top: 478px; background: var(--white); }

  .brand { position: absolute; display: flex; flex-direction: column; align-items: center; }
  .brand__row { display: flex; align-items: center; gap: 14px; }
  .brand__mark { width: 22px; height: 22px; border: 2px solid currentColor; }
  .brand__name { font-weight: 300; font-size: 42px; letter-spacing: 8px; line-height: 1; }
  .brand__tagline {
    margin-top: 8px; font-size: 9px; letter-spacing: 4.5px; font-weight: 500;
    padding: 3px 14px 4px; border-top: 1px solid currentColor; border-bottom: 1px solid currentColor;
  }

  .card--back .brand { left: 0; right: 0; top: 132px; color: var(--white); }
  .card--back .brand__mark { color: var(--gold); }
  .card--back .brand__tagline { color: var(--white); }

  .card--front .brand { left: 44px; top: 58px; color: var(--ink); }
  .card--front .brand__name { font-size: 38px; }
  .card--front .brand__mark { color: var(--gold); }
  .card--front .brand__tagline { color: var(--grey); border-color: var(--grey); }

  .card__band {
    position: absolute; left: 0; right: 0; bottom: 0; height: 160px;
    background: var(--charcoal); border-top: 8px solid var(--gold);
  }

  .person { position: absolute; right: 34px; top: 68px; text-align: right; }
  .person__name { color: var(--gold); font-weight: 600; font-size: 23px; letter-spacing: 1.5px; text-transform: uppercase; }
  .person__title { color: var(--ink); font-weight: 400; font-size: 16px; margin-top: 4px; }

  .contacts { position: absolute; right: 30px; bottom: 22px; list-style: none; }
  .contacts li {
    display: flex; justify-content: flex-end; align-items: center; gap: 12px;
    color: var(--white); font-size: 18px; line-height: 28px;
  }
  .contacts svg { width: 18px; height: 18px; stroke: var(--gold); fill: none; stroke-width: 1.6; }
  .contacts .accent { color: var(--gold); font-weight: 500; }
</style>
</head>
<body>

<section class="card card--back" aria-label="Business card back">
  <div class="brand">
    <div class="brand__row">
      <span class="brand__mark"></span>
      <span class="brand__name">BRISKEL</span>
    </div>
    <span class="brand__tagline">LUXURY LANDSCAPES</span>
  </div>
</section>

<section class="card card--front" aria-label="Business card front">
  <div class="card__band"></div>

  <div class="brand">
    <div class="brand__row">
      <span class="brand__mark"></span>
      <span class="brand__name">BRISKEL</span>
    </div>
    <span class="brand__tagline">LUXURY LANDSCAPES</span>
  </div>

  <div class="person">
    <h1 class="person__name">Tobias Fennick</h1>
    <p class="person__title">Co-Founder | Project Manager</p>
  </div>

  <ul class="contacts">
    <li>555-318-7094
      <svg viewBox="0 0 24 24"><circle cx="12" cy="12" r="10"/><path d="M8.5 7.5l2 2-1 1.5c.8 1.6 1.9 2.7 3.5 3.5l1.5-1 2 2-1.5 1.5c-3.5-.5-6.5-3.5-7-7z"/></svg>
    </li>
    <li>555-642-1586
      <svg viewBox="0 0 24 24"><rect x="7" y="3" width="10" height="18" rx="1.5"/><line x1="11" y1="18" x2="13" y2="18"/></svg>
    </li>
    <li>Tobias@briskel-example.ca
      <svg viewBox="0 0 24 24"><rect x="3" y="6" width="18" height="12"/><path d="M3 6l9 7 9-7"/></svg>
    </li>
    <li><span>WWW.<span class="accent">BRISKEL</span>.CA</span>
      <svg viewBox="0 0 24 24"><circle cx="12" cy="12" r="9"/><ellipse cx="12" cy="12" rx="4" ry="9"/><line x1="3" y1="12" x2="21" y2="12"/></svg>
    </li>
  </ul>
</section>

</body>
</html>
```